Lottery Website Design

Full website design, where you can take part on a lottery. Inkl Logo. The website is already developed: http://www.zorbel-ziehung.de
I like the modern fullscreen design from
http://www.marvestaplay.com/en-us/home.html
but the field for using the lottery right away should be present as well an the first screen like here:
https://www.glueckspfade.de/spiel/
Colour Scheme:
Red and Yellow?
Responsive design and coding (HTML & CSS).
The current website layout with bootstrap design ist http://www.zorbel-ziehung.de - the logo may be similar to favicon
Feel free to ask! :)
As always I am looking forward for your great ideas!
Updates
Reason: Not yet the best result found ...

```html
<!DOCTYPE html>
<html lang="de">
<head>
<meta charset="utf-8">
<title>Zorbel Ziehung</title>
<link href="https://fonts.googleapis.com/css2?family=Arimo:wght@400;700&display=swap" rel="stylesheet">
<style>
:root{
  --sky-top:#2d62b4;
  --sky-mid:#7aa6da;
  --sky-low:#e9eff7;
  --green:#5aa21a;
  --green-dark:#3f7f0f;
  --orange:#f2a62a;
  --orange-light:#f7c04a;
  --orange-deep:#d06a1c;
  --blue-text:#1b87c9;
  --sea-top:#9ccbe0;
  --sea-bottom:#3f7aa6;
  --heading-blue:#2f6a9c;
  --body-grey:#6b6b6b;
  --footer:#2f5e8a;
  --white:#fff;
}
*{margin:0;padding:0;box-sizing:border-box}
html,body{width:811px;height:1200px;overflow:hidden}
body{font-family:"Arimo",Arial,sans-serif;background:var(--white);position:relative}
.hero{position:absolute;left:0;top:0;width:811px;height:608px}
.hero-art{position:absolute;inset:0;background:linear-gradient(180deg,var(--sky-top) 0%,var(--sky-mid) 38%,var(--sky-low) 72%,var(--white) 100%)}
.brand{position:absolute;left:118px;top:27px;display:flex;align-items:center;gap:8px;color:var(--white)}
.brand-mark{width:40px;height:40px;border-radius:50%;background:var(--white)}
.brand-name{font-weight:700;font-size:17px;letter-spacing:.2px}
.brand-sub{font-size:9.5px;margin-top:5px}
.social-count{position:absolute;right:116px;top:52px;color:var(--white);font-size:10px}
.social-count b{font-size:14px;margin-right:3px}
.nav{position:absolute;left:116px;top:85px;width:580px;height:30px;border-radius:3px;
  background:linear-gradient(var(--green),var(--green-dark));display:flex;align-items:center;color:var(--white);font-size:8px;font-weight:700}
.nav a{color:var(--white);text-decoration:none;margin-left:30px;margin-right:20px}
.nav .status{margin-left:auto;font-size:6.5px;margin-right:9px}
.nav .btn{background:linear-gradient(var(--orange-light),var(--orange));color:#333;font-size:7px;padding:5px 0;width:54px;text-align:center;margin-right:3px;border-radius:2px}
.nav .btn:last-child{margin-right:10px}
.banner{position:absolute;left:116px;width:580px;height:42px;border-radius:3px;
  background:linear-gradient(var(--orange-light),var(--orange));color:var(--white);font-size:10px;
  display:flex;align-items:center;justify-content:center;letter-spacing:.2px}
.tiles{position:absolute;left:116px;top:180px;width:580px;display:grid;grid-template-columns:repeat(6,91px);column-gap:7px;row-gap:7px}
.tile{height:103px;border:1px solid #c9c9c9;position:relative;
  background-color:#ececec;
  background-image:linear-gradient(90deg,#d6d6d6 1px,transparent 1px),linear-gradient(#d6d6d6 1px,transparent 1px);
  background-size:13px 11px;background-position:3px 4px;
  display:flex;align-items:center;justify-content:center;font-size:62px;color:rgba(150,150,150,.45)}
.quick{position:absolute;left:116px;top:419px;width:580px;height:108px;border-radius:3px;
  background:linear-gradient(var(--orange) 0%,var(--orange-deep) 100%);color:var(--white)}
.quick h2{position:absolute;left:19px;top:14px;font-size:18px;font-weight:400}
.quick .adds{position:absolute;left:19px;top:42px;display:flex;gap:5px}
.quick .adds span{background:#f1d3a8;color:#a87a4a;font-size:7px;width:19px;height:15px;border-radius:2px;display:flex;align-items:center;justify-content:center}
.quick .adds svg{margin-left:4px}
.quick .meta{position:absolute;left:183px;font-size:7px;display:flex;align-items:center;gap:6px}
.box{width:9px;height:9px;background:#eee;border-radius:2px;display:inline-block}
.sum{position:absolute;left:0;width:811px;top:544px;text-align:center;color:var(--blue-text);font-size:10px;font-weight:700;line-height:18px}
.sea{position:absolute;left:0;top:608px;width:811px;height:327px;background:linear-gradient(var(--sea-top),var(--sea-bottom))}
.saved{position:absolute;left:0;width:811px;top:704px;text-align:center;color:var(--white);font-size:11.5px;font-weight:700}
.invite{position:absolute;left:150px;width:511px;top:729px;text-align:center;color:var(--white);font-size:8px;line-height:15px}
.rank{position:absolute;top:783px;width:197px;height:35px;background:linear-gradient(#7cc540,var(--green));color:var(--white);font-weight:700;font-size:10px;display:flex;align-items:center;padding-left:22px;border:1px solid var(--green-dark)}
.list{position:absolute;top:835px;list-style:none;color:var(--white);font-size:7.5px}
.list li{display:flex;align-items:center;gap:9px;height:18px}
.why{position:absolute;left:0;width:811px;top:966px;text-align:center;color:var(--heading-blue);font-size:12.5px;font-weight:700}
.why-text{position:absolute;left:138px;width:535px;top:992px;text-align:center;color:var(--body-grey);font-size:7.3px;line-height:14.4px}
.more{position:absolute;left:391px;top:1094px;width:28px;height:28px;border-radius:50%;border:1px solid #ccc;display:flex;align-items:center;justify-content:center}
.footer{position:absolute;left:0;top:1148px;width:811px;height:52px;background:var(--footer);color:var(--white);font-size:7px}
.footer p{position:absolute;left:118px;top:22px}
.footer .icons{position:absolute;left:600px;top:15px;display:flex;gap:7px}
.footer .icons span{width:19px;height:19px;border-radius:50%;background:var(--white)}
</style>
</head>
<body>
<section class="hero">
  <div class="hero-art" role="img" aria-label="Himmel mit Wolken als Hintergrundbild"></div>
  <div class="brand">
    <span class="brand-mark"></span>
    <div><div class="brand-name">ZORBEL ZIEHUNG (BETA)</div><div class="brand-sub">Kostenlose Lotto-Simulation mit Kostenkontrolle</div></div>
  </div>
  <div class="social-count"><b>Plaudernetz</b>: 2 people like this...</div>
  <nav class="nav">
    <a>INFOS</a><a>STARTSEITE</a><a>IMPRESSUM</a>
    <span class="status">SIE SIND NICHT EINGELOGGT.</span>
    <span class="btn">LOGIN</span><span class="btn">REGISTER</span>
  </nav>
  <div class="banner" style="top:126px">1. SCHRITT: ZAHLEN WÄHLEN, DIE KOSTENLOS BEI DER NÄCHSTEN ZIEHUNG GEPRÜFT WERDEN SOLLEN</div>
  <div class="tiles">
    <div class="tile">1</div><div class="tile">2</div><div class="tile">3</div><div class="tile">4</div><div class="tile">5</div><div class="tile">6</div>
    <div class="tile">7</div><div class="tile">8</div><div class="tile">9</div><div class="tile">10</div><div class="tile">11</div><div class="tile">12</div>
  </div>
  <div class="quick">
    <h2>QUICK TIPPS</h2>
    <div class="adds"><span>+1</span><span>+2</span><span>+4</span><span>+6</span><span>+12</span>
      <svg width="12" height="15" viewBox="0 0 12 15"><rect x="1" y="2" width="10" height="2" fill="#fff"/><rect x="4" y="0" width="4" height="2" fill="#fff"/><path d="M2 5h8l-1 10H3z" fill="#fff"/></svg></div>
    <div class="meta" style="top:21px">NÄCHSTE ZIEHUNG AM SAMSTAG, DEN 19.07.2014</div>
    <div class="meta" style="top:40px">Spieltage: <span class="box"></span> M1 <span class="box"></span> SA <span class="box"></span> M1+SA &nbsp;&nbsp;&nbsp;&nbsp;&nbsp;&nbsp; Laufzeit in Wochen: <span class="box"></span> 1 &nbsp; <span class="box"></span> 2 &nbsp; <span class="box"></span> 3 <span class="box"></span> 4 &nbsp; <span class="box"></span> 5</div>
    <div class="meta" style="top:60px;left:185px">Warum sind Felder ausgegraut?</div>
    <div class="meta" style="top:77px">Bonus 7: &nbsp;1 &nbsp;&nbsp; 2 &nbsp;&nbsp; 3 &nbsp;&nbsp; 4 &nbsp;&nbsp; 5 <span class="box"></span> &nbsp;&nbsp;&nbsp;&nbsp; Extra 6: &nbsp;1 &nbsp;&nbsp; 2 &nbsp;&nbsp; 3 &nbsp;&nbsp; 4 &nbsp;&nbsp; 5 <span class="box"></span> &nbsp;&nbsp;&nbsp;&nbsp; Superzahl: <span style="margin-left:72px">8</span></div>
  </div>
  <p class="sum">Würden Sie mit den Zahlen tatsächlich Lotto spielen (was mit Zorbel-Ziehung.de nicht geht<br>- hier ist alles kostenlos simuliert), wäre das ein Gesamtbetrag in Höhe von: 4.10 €</p>
</section>
<section class="sea"></section>
<div class="banner" style="top:639px">2. SCHRITT: MIT DIESEN ZAHLEN SOFORT LOSLEGEN (HIER KLICKEN)!</div>
<h2 class="saved">DURCH ZORBEL-ZIEHUNG.DE WURDEN BISHER 732,45 € GESPART.</h2>
<p class="invite">Wenn auch Sie wissen möchten, was gewesen wäre wenn Sie gespielt hätten, melden Sie sich gleich an und hinterlegen Sie Ihre persönlichen Zahlen für die nächste Ziehung.</p>
<div class="rank" style="left:194px">TOP 3 GESPART</div>
<div class="rank" style="left:420px">TOP 3 GLÜCKSPILZE</div>
<ul class="list" style="left:199px">
  <li><svg width="11" height="9"><path d="M1 5l3 3 6-7" stroke="#8fd13a" stroke-width="2" fill="none"/></svg>Mira (265,65€)</li>
  <li><svg width="11" height="9"><path d="M1 5l3 3 6-7" stroke="#8fd13a" stroke-width="2" fill="none"/></svg>Bernd K (202,75€)</li>
  <li><svg width="11" height="9"><path d="M1 5l3 3 6-7" stroke="#8fd13a" stroke-width="2" fill="none"/></svg>jmaxor (107,10€)</li>
</ul>
<ul class="list" style="left:425px">
  <li><svg width="11" height="9"><path d="M1 5l3 3 6-7" stroke="#8fd13a" stroke-width="2" fill="none"/></svg>lucky_-_jo (9,05€)</li>
  <li><svg width="11" height="9"><path d="M1 5l3 3 6-7" stroke="#8fd13a" stroke-width="2" fill="none"/></svg>Frau K (8,60€)</li>
  <li><svg width="11" height="9"><path d="M1 5l3 3 6-7" stroke="#8fd13a" stroke-width="2" fill="none"/></svg>Probe (0,40€)</li>
</ul>
<h2 class="why">WARUM ZORBEL ZIEHUNG?</h2>
<p class="why-text">Jede Woche am Mittwoch und am Samstag werden die Lottozahlen gezogen. Durchschnittlich 21 Millionen Deutsche warten dann darauf, dass genau ihre Zahlen von der Lottofee gezogen werden. Dennoch ist die Chance auf einen Gewinn nur 1:140 Millionen. Ein Sechser mit Superzahl ist unwahrscheinlicher als vom Blitz getroffen zu werden. Selbst ein Gewinn, der gerade einmal den Einsatz des Spiels wieder einbringt, hat eine Chance von nicht einmal zwei Prozent.Trotzdem holen sich Millionen von Menschen Lottoscheine und träumen vom großen Jackpot. Jede Woche Geld in einen Lottoschein zu investieren scheint auch keine große Summe zu sein und ab und an gewinnt man ja auch eine kleine Summe, die zumindest den aktuellen Einsatz wieder einspielt; vielleicht sogar etwas mehr? Und schon glaubt man wieder daran, doch einmal deutlich mehr zu gewinnen.</p>
<div class="more"><svg width="12" height="8"><path d="M1 1l5 5 5-5" stroke="#aaa" stroke-width="1.5" fill="none"/></svg></div>
<footer class="footer">
  <p>COPYRIGHT 2014.ZORBEL-ZIEHUNG.DE. ALL RIGHTS RESERVED.</p>
  <div class="icons"><span></span><span></span><span></span><span></span></div>
</footer>
</body>
</html>
```